Tech Startup needs Cool Business Card Designs

Looking for help Polishing our Business Card designs. We are a startup in the Knowledge management space that is releasing a product called TideNook which is a personal and group Digital Library. We're looking for help making our card designs standout. We already have a bunch of files to work from. Just need someone with an experienced eye to put everything together.

Target Market(s)

Knowledge Workers: people who work with alot of digital information on a daily basis and have problems keeping track and organizing everything. Special business cases; Researchers, Teacher/Trainers, Project Managers, Group Organizers, Nonprofit community managers, business owners, etc

Industry/Entity Type

Business

Contact Information for Business Card

Two Sided;
1) Backside is a digital library. I included several examples in the attached files. The digital library MUST use all of the ICONS attached. The digital library must look modern and sleek building off the concepts on the two attached files "BACK_'
2) Front- just needs to use the color scheme and style of the back into a modern hip yet professional design

Requirements
Must have
• - Designs for two sides
• - Back must be a representation of a digital library using ALL of the ICONS provided
• - Front must include all the main fields from Front business card design (but no QR code)
• - Must use TideNook Logo on both Front & Back
Should not have
• Do NOT NEED AREA FOR QR CODE

```html
<!DOCTYPE html>
<html lang="en">
<head>
<meta charset="utf-8">
<title>TideNook Business Card</title>
<link href="https://fonts.googleapis.com/css2?family=Nunito:wght@800&family=Raleway:wght@400;500;600&display=swap" rel="stylesheet">
<style>
  :root {
    --page-bg: #e9eaec;
    --card-white: #ffffff;
    --brand-blue: #2f74b5;
    --brand-blue-soft: #dce8f4;
    --brand-orange: #f0562a;
    --brand-orange-soft: #fde3da;
    --ink: #2b2f36;
    --ink-soft: #4a4f57;
    --shadow: rgba(20, 30, 45, 0.18);
  }
  * { box-sizing: border-box; margin: 0; padding: 0; }
  html, body { width: 1200px; height: 899px; overflow: hidden; }
  body {
    background: var(--page-bg);
    font-family: "Raleway", Arial, sans-serif;
    position: relative;
  }
  .card-slot {
    position: absolute;
    top: 295px;
    width: 540px;
    height: 308px;
  }
  .card-slot--front { left: 40px; }
  .card-slot--back { left: 620px; }
  .card {
    position: absolute;
    left: 0; top: 0;
    width: 900px;
    height: 514px;
    transform: scale(0.6);
    transform-origin: 0 0;
    border-radius: 42px;
    overflow: hidden;
    background: var(--card-white);
    box-shadow: 0 18px 40px var(--shadow);
  }
  .card-art { position: absolute; inset: 0; width: 100%; height: 100%; }
  .brand {
    position: absolute;
    display: flex;
    align-items: center;
    gap: 16px;
  }
  .card--front .brand { left: 300px; top: 96px; }
  .card--back .brand { left: 0; right: 0; top: 52px; justify-content: center; }
  .brand-dot {
    width: 34px; height: 34px;
    border-radius: 50%;
    background: var(--brand-orange);
  }
  .brand-name {
    font-family: "Nunito", Arial, sans-serif;
    font-weight: 800;
    font-size: 62px;
    letter-spacing: -0.5px;
    color: var(--brand-orange);
    line-height: 1;
  }
  .person {
    position: absolute;
    left: 500px;
    top: 222px;
    width: 320px;
    text-align: center;
  }
  .person-name {
    font-weight: 500;
    font-size: 28px;
    letter-spacing: 1.5px;
    color: var(--ink);
    text-transform: uppercase;
  }
  .person-title {
    font-weight: 500;
    font-size: 19px;
    color: var(--ink-soft);
    margin-top: 4px;
  }
  .contacts {
    position: absolute;
    left: 34px;
    top: 290px;
    list-style: none;
    color: var(--card-white);
    font-size: 19px;
    font-weight: 500;
  }
  .contact-item {
    display: flex;
    align-items: center;
    gap: 12px;
    height: 34px;
  }
  .contact-icon {
    width: 24px; height: 24px;
    border-radius: 50%;
    background: var(--card-white);
    display: flex;
    align-items: center;
    justify-content: center;
    flex: none;
  }
  .contact-icon svg { width: 14px; height: 14px; fill: var(--brand-blue); }
  .library-art {
    position: absolute;
    left: 90px;
    right: 90px;
    top: 150px;
    height: 260px;
    border-radius: 24px;
    background: linear-gradient(135deg, var(--brand-blue-soft), var(--brand-orange-soft));
  }
  .back-band {
    position: absolute;
    left: 0; right: 0; bottom: 0;
    height: 54px;
    background: var(--brand-blue);
    border-top: 10px solid var(--brand-orange);
  }
</style>
</head>
<body>
  <div class="card-slot card-slot--front">
    <section class="card card--front" aria-label="TideNook business card, front">
      <svg class="card-art" viewBox="0 0 900 514" preserveAspectRatio="none" aria-hidden="true">
        <path d="M0,212 C170,170 330,220 480,318 C620,408 760,425 900,372 L900,514 L0,514 Z" fill="var(--brand-blue)"/>
        <path d="M150,176 C300,162 410,235 510,300 C640,384 780,392 900,338 L900,356 C780,404 632,402 500,318 C400,254 300,186 150,176 Z" fill="var(--brand-orange)"/>
        <path d="M250,200 C370,214 450,272 540,320 C650,376 760,380 860,342 C760,392 645,388 535,330 C445,284 370,226 250,200 Z" fill="var(--brand-orange)"/>
      </svg>

      <div class="brand">
        <span class="brand-dot"></span>
        <span class="brand-name">TideNook</span>
      </div>

      <div class="person">
        <p class="person-name">Marcus Hale</p>
        <p class="person-title">Managing Director</p>
      </div>

      <ul class="contacts">
        <li class="contact-item">
          <span class="contact-icon"><svg viewBox="0 0 24 24"><path d="M6.6 10.8a15.1 15.1 0 0 0 6.6 6.6l2.2-2.2a1 1 0 0 1 1-.25 11.4 11.4 0 0 0 3.6.57 1 1 0 0 1 1 1V20a1 1 0 0 1-1 1A17 17 0 0 1 3 4a1 1 0 0 1 1-1h3.5a1 1 0 0 1 1 1c0 1.25.2 2.45.57 3.57a1 1 0 0 1-.25 1z"/></svg></span>
          012 555 0148
        </li>
        <li class="contact-item">
          <span class="contact-icon"><svg viewBox="0 0 24 24"><path d="M6.6 10.8a15.1 15.1 0 0 0 6.6 6.6l2.2-2.2a1 1 0 0 1 1-.25 11.4 11.4 0 0 0 3.6.57 1 1 0 0 1 1 1V20a1 1 0 0 1-1 1A17 17 0 0 1 3 4a1 1 0 0 1 1-1h3.5a1 1 0 0 1 1 1c0 1.25.2 2.45.57 3.57a1 1 0 0 1-.25 1z"/></svg></span>
          012 555 0148
        </li>
        <li class="contact-item">
          <span class="contact-icon"><svg viewBox="0 0 24 24"><path d="M3 5h18v14H3z M3 5l9 7 9-7" fill="none" stroke="var(--brand-blue)" stroke-width="2.4"/></svg></span>
          hello@tidenook.io
        </li>
        <li class="contact-item">
          <span class="contact-icon"><svg viewBox="0 0 24 24"><circle cx="12" cy="12" r="9" fill="none" stroke="var(--brand-blue)" stroke-width="2.4"/><path d="M3 12h18M12 3c3 3 3 15 0 18M12 3c-3 3-3 15 0 18" fill="none" stroke="var(--brand-blue)" stroke-width="2"/></svg></span>
          www.tidenook.io
        </li>
        <li class="contact-item">
          <span class="contact-icon"><svg viewBox="0 0 24 24"><path d="M12 2a7 7 0 0 0-7 7c0 5 7 13 7 13s7-8 7-13a7 7 0 0 0-7-7zm0 9.5A2.5 2.5 0 1 1 12 6.5a2.5 2.5 0 0 1 0 5z"/></svg></span>
          041 7th floor, Harbor Lane Road KTN
        </li>
      </ul>
    </section>
  </div>

  <div class="card-slot card-slot--back">
    <section class="card card--back" aria-label="TideNook business card, back">
      <div class="brand">
        <span class="brand-dot"></span>
        <span class="brand-name">TideNook</span>
      </div>
      <div class="library-art" role="img" aria-label="Digital library illustration: shelves holding the product icons"></div>
      <div class="back-band"></div>
    </section>
  </div>
</body>
</html>
```